Estate Agent Board Design

Most eye-catching, elegant estate agent board
Company logo should stand out
Korvimark & TREG should be small but visible.

On the board must be:

"FOR SALE"
logos
website zhbproperties.co.uk
tel number 01632 960418

It Company

```html
<!DOCTYPE html>
<html lang="en">
<head>
<meta charset="utf-8">
<title>zhb Sales &amp; Lettings – For Sale Board</title>
<link href="https://fonts.googleapis.com/css2?family=Montserrat:wght@500;600;700;800;900&display=swap" rel="stylesheet">
<style>
  :root {
    --backdrop: #eceeea;
    --board-frame: #a9aaa8;
    --board-face: #e4f1cf;
    --brand-dark: #1b5a2e;
    --brand-mid: #1f7a3a;
    --ink: #1c2a22;
    --white: #ffffff;
    --badge-blue: #1f66b8;
    --badge-navy: #1d2f6f;
  }
  * { box-sizing: border-box; margin: 0; padding: 0; }
  html, body {
    width: 1200px; height: 801px; overflow: hidden;
    background: var(--backdrop);
    font-family: "Montserrat", sans-serif;
  }
  .sale-board {
    position: absolute; left: 335px; top: 50px;
    width: 530px; height: 700px;
    background: var(--board-face);
    border: 7px solid var(--board-frame);
    box-shadow: 0 6px 18px rgba(0,0,0,.18);
  }
  .brand {
    position: absolute; left: 52px; top: 60px;
    display: flex; align-items: flex-start; gap: 18px;
  }
  .brand-square {
    width: 158px; height: 158px; background: var(--brand-dark);
  }
  .brand-text { display: flex; flex-direction: column; }
  .brand-name {
    font-weight: 900; font-size: 132px; line-height: 1;
    letter-spacing: -4px; color: var(--brand-dark);
    margin-top: -6px;
  }
  .brand-tagline {
    font-weight: 600; font-size: 21px; color: var(--ink);
    margin-top: 6px; letter-spacing: .2px;
  }
  .sale-band {
    position: absolute; left: 0; right: 0; top: 274px; height: 178px;
    background: var(--brand-dark);
    display: flex; flex-direction: column; align-items: center; justify-content: center;
    color: var(--white); font-weight: 800; font-size: 72px; line-height: .98;
    letter-spacing: 2px;
  }
  .phone {
    position: absolute; left: 0; right: 0; top: 488px;
    display: flex; justify-content: center; align-items: center; gap: 8px;
    font-weight: 700; font-size: 40px; color: var(--ink); letter-spacing: 1.5px;
  }
  .phone svg { width: 34px; height: 34px; }
  .badges {
    position: absolute; left: 0; right: 0; top: 560px;
    display: flex; justify-content: center; gap: 14px;
  }
  .badge { width: 60px; height: 60px; border-radius: 50%; }
  .badge--korvimark { background: var(--badge-navy); }
  .badge--treg { background: var(--badge-blue); border: 4px solid var(--badge-navy); }
  .website {
    position: absolute; left: 0; right: 0; top: 648px; text-align: center;
    font-weight: 500; font-size: 21px; letter-spacing: 3px; color: var(--ink);
  }
  .website strong { font-weight: 700; color: var(--brand-mid); }
</style>
</head>
<body>
  <div class="sale-board">
    <div class="brand">
      <div class="brand-square"></div>
      <div class="brand-text">
        <span class="brand-name">zhb</span>
        <span class="brand-tagline">SALES &amp; LETTINGS</span>
      </div>
    </div>

    <div class="sale-band">
      <span>FOR</span>
      <span>SALE</span>
    </div>

    <div class="phone">
      <svg viewBox="0 0 24 24" aria-hidden="true">
        <path fill="#1f7a3a" d="M6.6 2.5c.6-.4 1.4-.3 1.8.3l2 3c.4.6.3 1.3-.2 1.8L8.9 8.8c.9 2.5 3 4.9 5.3 6.2l1.3-1.3c.5-.5 1.2-.6 1.8-.2l3 2c.6.4.7 1.2.3 1.8l-1.5 2.2c-.5.8-1.5 1.1-2.4.8C10.5 18.2 5.8 13.5 3.7 7.4c-.3-.9 0-1.9.8-2.4z"/>
      </svg>
      <span>01632 960418</span>
    </div>

    <div class="badges">
      <div class="badge badge--korvimark" aria-label="Korvimark accreditation"></div>
      <div class="badge badge--treg" aria-label="TREG accreditation"></div>
    </div>

    <div class="website">www.<strong>zhbproperties</strong>.co.uk</div>
  </div>
</body>
</html>
```